Residential Remodeling Contractor needs updated business card

I need a new design for my business card.
Name of the company is Ridgefell Construction. I need a card that commands presence, strength, integrity. I have been in business for 28 years. I am a Residential Remodeling Contractor that covers all aspects of a residential remodel and build.

```html
<!DOCTYPE html>
<html lang="en">
<head>
<meta charset="utf-8">
<title>Ridgefell Construction – Business Card</title>
<link href="https://fonts.googleapis.com/css2?family=Libre+Baskerville:wght@700&family=Arimo:wght@400&display=swap" rel="stylesheet">
<style>
  :root {
    --page-bg: #e7e9ee;
    --card-blue: #1c3f84;
    --card-blue-back: #203f88;
    --emboss-blue: #17336f;
    --ink-white: #ffffff;
    --shadow: rgba(10, 20, 50, 0.28);
  }
  * { box-sizing: border-box; margin: 0; padding: 0; }
  html, body {
    width: 1200px;
    height: 912px;
    overflow: hidden;
    background: var(--page-bg);
  }
  .canvas {
    width: 1200px;
    height: 912px;
    display: flex;
    flex-direction: column;
    align-items: center;
    justify-content: center;
    gap: 32px;
  }
  .card {
    position: relative;
    width: 700px;
    height: 400px;
    border-radius: 22px;
    overflow: hidden;
    box-shadow: 0 10px 26px var(--shadow);
  }

  /* Back side */
  .card--back {
    background: var(--card-blue-back);
    display: flex;
    align-items: center;
    justify-content: center;
  }
  .card--back .brand-name {
    font-family: "Libre Baskerville", Georgia, serif;
    font-weight: 700;
    font-size: 40px;
    line-height: 1.15;
    letter-spacing: 2px;
    text-transform: uppercase;
    color: var(--emboss-blue);
    text-align: left;
  }

  /* Front side */
  .card--front {
    background: var(--card-blue);
    color: var(--ink-white);
  }
  .card--front .brand {
    position: absolute;
    left: 60px;
    top: 50px;
    display: flex;
    align-items: center;
    gap: 16px;
  }
  .brand-square {
    width: 22px;
    height: 22px;
    background: var(--ink-white);
  }
  .card--front .brand-name {
    font-family: "Libre Baskerville", Georgia, serif;
    font-weight: 700;
    font-size: 26px;
    line-height: 1.15;
    letter-spacing: 1.5px;
    text-transform: uppercase;
    color: var(--ink-white);
  }
  .accent-bar {
    position: absolute;
    left: 0;
    top: 200px;
    width: 40px;
    height: 62px;
    background: var(--ink-white);
  }
  .contact-block {
    position: absolute;
    left: 60px;
    top: 168px;
  }
  .person-name {
    font-family: "Libre Baskerville", Georgia, serif;
    font-weight: 700;
    font-size: 24px;
    letter-spacing: 1px;
    text-transform: uppercase;
  }
  .person-title,
  .address,
  .contact-list {
    font-family: "Arimo", Arial, sans-serif;
    font-size: 15px;
    line-height: 1.4;
  }
  .person-title { margin-top: 2px; }
  .address { margin-top: 16px; }
  .contact-list {
    list-style: none;
    margin-top: 18px;
  }
  .contact-list li {
    display: flex;
    align-items: center;
    gap: 10px;
    margin-bottom: 4px;
  }
  .contact-list svg {
    width: 14px;
    height: 14px;
    flex: none;
    fill: var(--ink-white);
  }
</style>
</head>
<body>
  <main class="canvas">
    <section class="card card--back" aria-label="Card back">
      <p class="brand-name">Ridgefell<br>Construction</p>
    </section>

    <section class="card card--front" aria-label="Card front">
      <div class="brand">
        <span class="brand-square"></span>
        <p class="brand-name">Ridgefell<br>Construction</p>
      </div>

      <span class="accent-bar"></span>

      <div class="contact-block">
        <h1 class="person-name">Daniel Arbuckle</h1>
        <p class="person-title">Owner &amp; Manager</p>
        <p class="address">P.O. Box 418 Alder Street<br>Brookvale AB, T4N 2K7</p>
        <ul class="contact-list">
          <li>
            <svg viewBox="0 0 24 24" aria-hidden="true"><path d="M6.6 10.8a15.1 15.1 0 0 0 6.6 6.6l2.2-2.2a1 1 0 0 1 1-.25 11.4 11.4 0 0 0 3.6.57 1 1 0 0 1 1 1V20a1 1 0 0 1-1 1A17 17 0 0 1 3 4a1 1 0 0 1 1-1h3.5a1 1 0 0 1 1 1c0 1.25.2 2.45.57 3.57a1 1 0 0 1-.25 1z"/></svg>
            <span>555 014 2290</span>
          </li>
          <li>
            <svg viewBox="0 0 24 24" aria-hidden="true"><path d="M2 5h20v14H2z M4 7v.5l8 5 8-5V7l-8 5z" fill-rule="evenodd"/></svg>
            <span>info@ridgefellconstruction.com</span>
          </li>
          <li>
            <svg viewBox="0 0 24 24" aria-hidden="true"><path d="M12 2a10 10 0 1 0 0 20 10 10 0 0 0 0-20zm0 2c.9 0 2.2 1.9 2.7 5H9.3C9.8 5.9 11.1 4 12 4zm-3 7h6a18 18 0 0 1 0 2H9a18 18 0 0 1 0-2zm.3 4h5.4c-.5 3.1-1.8 5-2.7 5s-2.2-1.9-2.7-5z"/></svg>
            <span>www.ridgefellconstruction.com</span>
          </li>
        </ul>
      </div>
    </section>
  </main>
</body>
</html>
```